Website development company website

ABOUT COMPANY
Hi everyone! We're a Melbourne, Australia website development company in a need of a website design that will make online store merchants want to engage our services.
We specialise exclusively in Torvista e-commerce platform (https://torvista-platform.example/). What distinguishes our business from competition is that rather than designing and building brand new websites, we offer development, support and maintenance services to established websites. Maintenance and Support are the keywords representing our business.
Our potential clients are people with broken, slow and underperforming Torvista installations who need assistance getting their websites up and making sales. Our website must pass the message that we can help, and provide quick means of making contact.
DESIGN
Overall, we're looking for a slick, clean, airy, conservative design. No need to do anything crazy, try to stick to what's "standard" in website design these days and make it easy on all of us. The website is unlikely to be updated too often so it needs to look attractive and fresh first time over and after a year, too.
Attached is our new logo, which you'll be able to take the basic idea from, the colors and fonts. Though, don't use the fonts from the logo in the website, stick to the standard widely supported fonts. Additional use of Google fonts is fine.
Don't overdo it with colors, stick to conservative basic color set and only use the colors from the log for accents like headings etc. Please, don't be tempted to use the blue and orange as background of whole blocks, other than perhaps footer. Thanks.
For the images used, I'd like to stay away from a design studio/digital agency feel and lean more towards professional support and maintenance services. I'm thinking images of content merchants doing their job. Something along the lines of "We'll be taking care of the website so that you only need to care about the business".
Some ideas I like:
http://www.plumframe-pics.example/detail/photo/portrait-of-confident-male-design-professional-royalty-free-image/572048163
http://www.plumframe-pics.example/detail/photo/designer-taking-picture-of-hat-high-res-stock-photography/839207514
http://www.plumframe-pics.example/detail/photo/woman-packaging-pottery-royalty-free-image/216684093
Images of colorful shopping bags and shopping carts are over the top and not serious enough. Instead of images matching Online Shopping, I'd try going more for Stability, Reliability, Performance.
Our existing website is http://www.bravuln.example. Please, don't take design ideas from it, but it will give you a picture of the structure of our new website and content that's going to be used initially.
If you could include a basic icon set to use throughout the website, that would be great. If the icons could match our logo (attached), it would be a big plus.
ALL PAGES
Every page must contain clearly visible phone number (1300 648 907) and a Contact Us Now button, which opens an AJAX driven popup form with Name, Email, Phone and Message to be sent through.
To start with, main menu items will be Torvista, Portfolio, Contact.
At the bottom of each page, please, include a newsletter subscription form with text Subscribe to Torvista Support and Security Updates.
For the footer, I'd like to see a logo strip with the following logos in grayscale (no need to link anywhere): Torvista, QRX, DataVane, NCB. You'll find the logos on Google Images.
Standard footer columns follow. Here, I'd like to see logos in color: Torvista Certified Developer, Torvista Ceritified Solution Provider. Again, the logos are on Google Images.
No social media logos/links necessary anywhere on the website.
...and then the copyright line.
FRONT PAGE
Large slider with images that would appeal to our target audience. Keywords here would be Torvista System Audit, Torvista Performance Optimisation, Torvista Website Emergency Recovery, Torvista Development Infrastructure Hosting. We'll have a static page created for each of these to link to.
In a corner of the slider, or on the edge, can I have an overlay with logos in color (same as footer): Torvista Certified Developer, Torvista Ceritified Solution Provider.
Underneath, a number of blocks, each with an image and teaser that we'll use to link to various pages throughout the website.
PORTFOLIO PAGE
I'm thinking a single long page with a block per client, which will contain project name, description from us and a testimonial from client. Also, each block will contain a single large screenshot. No gallery or slideshow is necessary here, just one image per project.
I'll leave the layout up to you, but try to put yourself in the shoes of a potential client reviewing our past work by simply scrolling down this one page.
CONTACT US PAGE
Separate page with the same form as above, phone number (1300 648 907), email address (support@kavreo.example), address (Suite 42, Level 3|8 Wattlebrook Lane|Fernvale Heights VIC 3999), and a grayscale Google Map.
CODING UP
Coding up into static HTML/CSS/JS is equally important as the design itself. We're a website development company, we'll be integrating the theme. We will spot any issues and we will point them out.
Coded up design must be fully responsive. Enough said.
To be able to create any content in future, we'd like one extra page coded up with samples of all themed elements, lists, forms, buttons, 2, 3, 4-column layout, alerts, icons, etc. This page does not need to be designed, only coded up.
The design will be integrated into Drupal using Twig. If possible at all, try to keep it in mind when designing and coding up, and make the integration into a Drupal theme easier for us.
GOOD LUCK!
That's it. Let me know if anything needs clarifying. So far I've had a great experience with ArtFlockly. I don't doubt some great designs will emerge. Clever ideas are highly appreciated, but also make it clear you've read and followed the points in this brief. Cheers, Tom

```html
<!DOCTYPE html>
<html lang="en">
<head>
<meta charset="utf-8">
<title>Kavreo – Torvista Development, Support and Maintenance</title>
<link rel="stylesheet" href="https://fonts.googleapis.com/css2?family=Open+Sans:wght@400;600;700&display=swap">
<style>
:root{
  --blue:#1c5ea8;
  --blue-dark:#15477f;
  --orange:#ef7d1b;
  --ink:#222;
  --muted:#666;
  --light:#ececec;
  --white:#fff;
  --charcoal:#1f1f1f;
  --charcoal-2:#2b2b2b;
}
*{box-sizing:border-box;margin:0;padding:0}
html,body{width:1200px;height:2740px;overflow:hidden}
body{font-family:"Open Sans",Arial,sans-serif;color:var(--ink);background:var(--white);position:relative}
a{color:inherit;text-decoration:none}

/* header */
.site-header{height:88px;border-top:5px solid var(--orange);display:flex;align-items:center;padding:0 40px;background:var(--white)}
.brand{display:flex;align-items:center;gap:10px;font-weight:700;font-size:34px;color:var(--blue)}
.brand-mark{width:18px;height:18px;background:var(--orange)}
.site-title{font-size:30px;font-weight:700;margin-left:40px;color:var(--ink)}
.main-nav{margin-left:auto;display:flex;gap:0}
.main-nav a{font-size:15px;padding:8px 22px;color:#555;border-left:1px solid #ddd}
.main-nav a:first-child{border-left:none;color:var(--ink);font-weight:600;border-bottom:2px solid var(--orange)}

/* hero */
.hero{position:relative;height:492px}
.hero-photo{position:absolute;inset:0;background:linear-gradient(100deg,#c9ccd0 0%,#8a8f96 35%,#5b6470 60%,#a9adb3 100%)}
.hero-caption{position:absolute;top:308px;left:0;right:0;text-align:center;color:var(--white);font-size:27px;font-weight:600;text-shadow:0 1px 3px rgba(0,0,0,.4)}
.slider-arrow{position:absolute;top:175px;width:30px;height:30px;background:rgba(255,255,255,.75);display:flex;align-items:center;justify-content:center}
.slider-arrow.prev{left:18px}.slider-arrow.next{right:18px}
.tech-strip{position:absolute;left:0;right:0;bottom:0;height:108px;background:rgba(20,20,20,.85);display:flex;align-items:center;justify-content:center;gap:78px}
.tech-name{color:var(--white);font-size:30px;font-weight:600}

/* certifications */
.certs{height:332px;display:flex;justify-content:center;gap:80px;padding-top:20px}
.cert-card{width:420px;height:240px;background:linear-gradient(135deg,#2a6ab2,#14457e);color:var(--white);text-align:center;padding-top:82px}
.cert-card h3{font-size:22px;font-weight:600;margin-bottom:8px}
.cert-card p{font-size:13px;opacity:.85;margin-bottom:14px}
.btn{display:inline-block;background:var(--orange);color:var(--white);font-size:13px;font-weight:600;padding:7px 20px;border-radius:3px}

/* section headings */
.section-title{text-align:center;font-size:34px;font-weight:700}
.section-title span{color:var(--orange)}
.title-mark{width:14px;height:14px;margin:14px auto 0;background:var(--ink);border-radius:50%}

/* services */
.services{height:588px;background:var(--light);padding-top:150px}
.service-list{display:flex;justify-content:center;gap:110px;margin-top:50px}
.service{width:250px;text-align:center}
.service-icon{width:104px;height:104px;border:4px solid var(--orange);border-radius:50%;margin:0 auto 18px;display:flex;align-items:center;justify-content:center;background:var(--white)}
.service h3{font-size:19px;color:var(--blue);font-weight:700;margin-bottom:8px}
.service p{font-size:13px;color:var(--muted);line-height:1.55;margin-bottom:16px}

/* portfolio */
.portfolio{height:440px;background:var(--orange);padding-top:44px;position:relative}
.portfolio .section-title{color:var(--white)}
.portfolio .title-mark{background:var(--ink)}
.project-row{display:flex;justify-content:center;gap:16px;margin-top:52px}
.project-shot{width:220px;height:250px;border:4px solid var(--white)}
.project-shot.p1{background:linear-gradient(#1d2230,#33405a)}
.project-shot.p2{background:linear-gradient(#3c3a31,#676040)}
.project-shot.p3{background:linear-gradient(#eef5e4,#8cc45a)}
.project-shot.p4{background:linear-gradient(#f2f2f2,#7fb7d9)}
.project-shot.p5{background:linear-gradient(#e9faf6,#47c9b0)}
.row-arrow{position:absolute;top:250px;color:var(--white)}
.row-arrow.prev{left:60px}.row-arrow.next{right:60px}

/* testimonials */
.testimonials{height:340px;padding-top:32px;position:relative;text-align:center}
.avatar{width:96px;height:96px;border-radius:50%;border:4px solid var(--orange);background:linear-gradient(#d9d2c8,#9a8f82);margin:30px auto 14px}
.client-name{color:var(--blue);font-weight:700;font-size:17px;margin-bottom:8px}
.quote{width:940px;margin:0 auto;font-size:12.5px;color:var(--muted);line-height:1.6}
.testimonials .row-arrow{top:150px;color:#888}

/* partner strip */
.partner-strip{height:92px;background:var(--charcoal-2);display:flex;align-items:center;justify-content:center;gap:78px}

/* footer */
.site-footer{height:320px;background:var(--charcoal);color:#cfcfcf;display:flex;gap:40px;padding:44px 60px 0}
.footer-col{flex:1}
.footer-col h4{color:var(--white);font-size:16px;font-weight:700;margin-bottom:20px}
.quick-links li{list-style:none;font-size:13px;padding:5px 0 5px 14px;position:relative}
.quick-links li::before{content:"";position:absolute;left:0;top:12px;width:5px;height:5px;background:var(--orange)}
.quick-links li:first-child{color:var(--orange)}
.contact-line{display:flex;gap:10px;font-size:13px;line-height:1.5;margin-bottom:12px}
.contact-line svg{flex:none;margin-top:3px}
.field{background:var(--white);height:28px;margin-bottom:10px;color:#999;font-size:12px;padding:6px 10px}
.field.message{height:52px}
.submit{display:inline-block;background:var(--orange);color:var(--white);font-size:12px;font-weight:600;padding:5px 18px}
.map{height:180px;background:linear-gradient(135deg,#dcdcdc,#b8b8b8)}
.copyright{height:28px;background:#151515;color:#aaa;font-size:11px;display:flex;align-items:center;justify-content:center}
</style>
</head>
<body>

<header class="site-header">
  <a class="brand" href="#"><span class="brand-mark"></span>Kavreo</a>
  <div class="site-title">Kavreo</div>
  <nav class="main-nav">
    <a href="#">Home</a><a href="#">Torvista</a><a href="#">Torvista</a><a href="#">Portfolio</a><a href="#">Contacts</a>
  </nav>
</header>

<section class="hero">
  <div class="hero-photo" role="img" aria-label="Photo of a smiling business team gathered around a laptop"></div>
  <a class="slider-arrow prev" href="#"><svg width="12" height="14"><path d="M9 1 3 7l6 6" fill="none" stroke="#333" stroke-width="2"/></svg></a>
  <a class="slider-arrow next" href="#"><svg width="12" height="14"><path d="M3 1l6 6-6 6" fill="none" stroke="#333" stroke-width="2"/></svg></a>
  <p class="hero-caption">High performance Torvista sites on time and on budget.</p>
  <div class="tech-strip">
    <span class="tech-name">Markwell</span><span class="tech-name">Torvista</span><span class="tech-name">Brewlet</span><span class="tech-name">QRX</span><span class="tech-name">NCB</span><span class="tech-name">DataVane</span>
  </div>
</section>

<section class="certs">
  <div class="cert-card">
    <h3>Torvista Certified Developer</h3>
    <p>Trusted experts in platform builds and upgrades.</p>
    <a class="btn" href="#">Read More</a>
  </div>
  <div class="cert-card">
    <h3>Torvista Ceritified Solution Provider</h3>
    <p>Certified partner for complete store solutions.</p>
    <a class="btn" href="#">Read More</a>
  </div>
</section>

<section class="services">
  <h2 class="section-title">Our <span>Services</span></h2>
  <div class="title-mark"></div>
  <div class="service-list">
    <div class="service">
      <div class="service-icon"><svg width="50" height="50" viewBox="0 0 50 50" fill="none" stroke="#333" stroke-width="3"><circle cx="25" cy="25" r="20"/><path d="M5 25h40M25 5c-8 10-8 30 0 40M25 5c8 10 8 30 0 40"/></svg></div>
      <h3>Web development</h3>
      <p>Custom modules, themes and integrations built to keep your online store fast, stable and ready to sell every day.</p>
      <a class="btn" href="#">Read More</a>
    </div>
    <div class="service">
      <div class="service-icon"><svg width="50" height="50" viewBox="0 0 50 50" fill="none" stroke="#333" stroke-width="3"><circle cx="25" cy="25" r="20"/><circle cx="25" cy="25" r="9"/><path d="M11 11l8 8M39 11l-8 8M11 39l8-8M39 39l-8-8"/></svg></div>
      <h3>Web support</h3>
      <p>Fast help when your store breaks, slows down or stops taking orders, with clear answers from real platform experts.</p>
      <a class="btn" href="#">Read More</a>
    </div>
    <div class="service">
      <div class="service-icon"><svg width="50" height="50" viewBox="0 0 50 50" fill="none" stroke="#333" stroke-width="3"><path d="M10 40l18-18M30 8a9 9 0 0 0 12 12l-6 6-12-12z"/><path d="M40 40 24 24M8 10l6-2 4 4-2 6z"/></svg></div>
      <h3>Web maintenance</h3>
      <p>Regular updates, security patches and health checks that keep your installation secure and running smoothly all year.</p>
      <a class="btn" href="#">Read More</a>
    </div>
  </div>
</section>

<section class="portfolio">
  <h2 class="section-title">Our Portfolio</h2>
  <div class="title-mark"></div>
  <span class="row-arrow prev"><svg width="14" height="22"><path d="M12 2 3 11l9 9" fill="none" stroke="currentColor" stroke-width="2.5"/></svg></span>
  <span class="row-arrow next"><svg width="14" height="22"><path d="M2 2l9 9-9 9" fill="none" stroke="currentColor" stroke-width="2.5"/></svg></span>
  <div class="project-row">
    <div class="project-shot p1" role="img" aria-label="Screenshot of a dark themed online store"></div>
    <div class="project-shot p2" role="img" aria-label="Screenshot of an outdoor gear store homepage"></div>
    <div class="project-shot p3" role="img" aria-label="Screenshot of a green grocery store website"></div>
    <div class="project-shot p4" role="img" aria-label="Screenshot of a product catalogue page"></div>
    <div class="project-shot p5" role="img" aria-label="Screenshot of a teal landing page"></div>
  </div>
</section>

<section class="testimonials">
  <h2 class="section-title">Client <span>Testimonials</span></h2>
  <div class="title-mark"></div>
  <span class="row-arrow prev"><svg width="14" height="22"><path d="M12 2 3 11l9 9" fill="none" stroke="currentColor" stroke-width="2.5"/></svg></span>
  <span class="row-arrow next"><svg width="14" height="22"><path d="M2 2l9 9-9 9" fill="none" stroke="currentColor" stroke-width="2.5"/></svg></span>
  <div class="avatar" role="img" aria-label="Client portrait"></div>
  <p class="client-name">Vestibulum porta</p>
  <p class="quote">The team rescued our store after a failed upgrade and have kept it running smoothly ever since. Response times are quick, advice is clear and sales have grown steadily. We can finally focus on our business instead of the website.</p>
</section>

<div class="partner-strip">
  <span class="tech-name">Markwell</span><span class="tech-name">Torvista</span><span class="tech-name">Brewlet</span><span class="tech-name">QRX</span><span class="tech-name">NCB</span><span class="tech-name">DataVane</span>
</div>

<footer class="site-footer">
  <div class="footer-col">
    <h4>Quick Links</h4>
    <ul class="quick-links">
      <li>Home</li><li>About Us</li><li>Torvista</li><li>Portfolio</li><li>Contact Us</li>
    </ul>
  </div>
  <div class="footer-col">
    <h4>Address</h4>
    <div class="contact-line"><svg width="12" height="16" viewBox="0 0 12 16"><path d="M6 0a6 6 0 0 0-6 6c0 4 6 10 6 10s6-6 6-10a6 6 0 0 0-6-6z" fill="#ef7d1b"/><circle cx="6" cy="6" r="2" fill="#1f1f1f"/></svg><span>Kavreo<br>Suite 42, Level 3<br>8 Wattlebrook Lane<br>Fernvale Heights VIC 3999</span></div>
    <div class="contact-line"><svg width="14" height="14" viewBox="0 0 14 14"><path d="M3 0l3 3-2 2c1 2 3 4 5 5l2-2 3 3-2 3C6 14 0 8 0 2z" fill="#ef7d1b"/></svg><span>1300 648 907</span></div>
    <div class="contact-line"><svg width="14" height="12" viewBox="0 0 14 12"><rect x="0" y="1" width="14" height="10" fill="#ef7d1b"/><path d="M0 1l7 6 7-6" fill="none" stroke="#1f1f1f" stroke-width="1.4"/></svg><span>support@kavreo.example</span></div>
  </div>
  <div class="footer-col">
    <h4>Get In Touch</h4>
    <div class="field">Name</div>
    <div class="field">Email</div>
    <div class="field message">Message</div>
    <span class="submit">Submit</span>
  </div>
  <div class="footer-col">
    <h4>Location Map</h4>
    <div class="map" role="img" aria-label="Grayscale street map showing the office location"></div>
  </div>
</footer>
<div class="copyright">Copyright © 2016 Kavreo. All rights reserved.</div>

</body>
</html>
```